Quick Straightforward Billboard Redesign

- Design billboard sized for 10 foot' x 36' foot width live area size and please include bleeds 6" around all sides
- Exact blue color match is imperative in headline, logo, phone number bubble or wherever used. C-83 / M-45 / Y-1 / K-0-
- What I hope to illustrate is that our company offers the best porch screening in the area area, in regards to quality, expertise, durability, storms proof, but we do not build screen porches.
- Current board is attached below from previous designer, and as you can see sizing was off, white space on edges make it appear to be sized incorrectly.
- I also attached my own little mock up idea well well if it helps, favorite image, logo, headline, etc and ideas perhaps on expanding or making this better?

Thanks so much!

Target Market(s)

Drivers and passengers, Southeastern NC, are of immense new construction and high end homes.

Industry/Entity Type

Construction

Colors
0054AA
0677BA
7BADD7
CADEEF
E8F1F8

Requirements
Must have
• Blue color matching
Nice to have
• Design spins or other thoughts on my little mock up

```html
<!DOCTYPE html>
<html lang="en">
<head>
<meta charset="utf-8">
<title>Tidewater Co. Billboard</title>
<link href="https://fonts.googleapis.com/css2?family=Archivo+Black&family=Oswald:wght@700&display=swap" rel="stylesheet">
<style>
  :root {
    --brand-blue: #1f5fa6;
    --brand-green: #2a9a4a;
    --paper: #f1f1ef;
    --stage: #e8f1f8;
    --white: #ffffff;
    --photo-sky: #8fb4d8;
    --photo-stone: #b9b2a4;
    --photo-wicker: #5d5347;
  }
  * { margin: 0; padding: 0; box-sizing: border-box; }
  html, body { width: 1200px; height: 512px; overflow: hidden; }
  body { background: var(--stage); position: relative; }

  .billboard {
    position: absolute;
    left: 0; top: 100px;
    width: 1200px; height: 312px;
    display: flex;
    background: var(--paper);
  }
  .porch-photo {
    width: 426px; height: 100%;
    background: linear-gradient(180deg, var(--white) 0%, var(--photo-sky) 22%, #7fa06a 45%, var(--photo-wicker) 62%, var(--photo-stone) 100%);
  }
  .message { flex: 1; display: flex; flex-direction: column; }
  .headline-band {
    height: 162px;
    background: var(--brand-blue);
    display: flex; align-items: center; justify-content: center;
  }
  .headline {
    font-family: "Archivo Black", sans-serif;
    color: var(--white);
    font-size: 51px;
    line-height: 1.12;
    letter-spacing: 0.5px;
    text-align: left;
    padding-top: 4px;
  }
  .contact-row {
    flex: 1;
    display: flex; align-items: center;
    padding: 0 34px 0 31px;
    justify-content: space-between;
  }
  .company-name {
    font-family: "Archivo Black", sans-serif;
    color: var(--brand-blue);
    font-size: 26px;
    line-height: 1;
    white-space: nowrap;
  }
  .phone-pill {
    display: flex;
    width: 424px; height: 93px;
    border-radius: 12px;
    background: var(--brand-blue);
    overflow: hidden;
  }
  .phone-icon {
    width: 68px;
    display: flex; align-items: center; justify-content: center;
  }
  .phone-number {
    flex: 1;
    background: var(--brand-green);
    border-radius: 12px;
    color: var(--white);
    font-family: "Oswald", sans-serif;
    font-weight: 700;
    font-size: 58px;
    letter-spacing: 1px;
    display: flex; align-items: center; justify-content: center;
  }
</style>
</head>
<body>
  <section class="billboard">
    <div class="porch-photo" role="img" aria-label="Photo of a covered coastal porch with wicker seating overlooking a lawn and lake"></div>
    <div class="message">
      <div class="headline-band">
        <h1 class="headline">SCREEN YOUR PORCH<br>BUILT FOR THE COAST</h1>
      </div>
      <div class="contact-row">
        <p class="company-name">Tidewater Co.</p>
        <div class="phone-pill">
          <div class="phone-icon">
            <svg width="40" height="40" viewBox="0 0 24 24" aria-hidden="true">
              <path d="M6.6 3.5c.6 0 1 .3 1.2.8l1.2 3c.2.5 0 1-.3 1.4L7.3 10c1.2 2.6 3.2 4.6 5.8 5.8l1.3-1.4c.4-.4.9-.5 1.4-.3l3 1.2c.5.2.8.6.8 1.2v2.6c0 .8-.6 1.4-1.4 1.4C9.9 20.5 3.5 14.1 3.5 5c0-.8.6-1.5 1.4-1.5z" fill="#ffffff"/>
            </svg>
          </div>
          <div class="phone-number">910.555.0142</div>
        </div>
      </div>
    </div>
  </section>
</body>
</html>
```